furniture and home contents restoration

I need to list the services that we perform in our studio.
we serve the general public as well as the insurance/ remediation industry

```html
<!DOCTYPE html>
<html lang="en">
<head>
<meta charset="utf-8">
<title>Hallmere Refinishers – Business Card</title>
<link rel="stylesheet" href="https://fonts.googleapis.com/css2?family=Rubik:wght@400;500;700&family=Roboto+Condensed:wght@400;500;700&display=swap">
<style>
  :root {
    --backdrop: #3a3c40;
    --card-dark: #1f2d35;
    --card-light: #ffffff;
    --ink-light: #f2f4f5;
    --ink-muted: #c9d1d5;
    --brand-faint: #33454f;
    --divider: #8e9aa0;
    --ink-dark: #1f2d35;
  }
  * { margin: 0; padding: 0; box-sizing: border-box; }
  html, body { width: 1200px; height: 801px; overflow: hidden; }
  body {
    background: var(--backdrop);
    display: flex;
    align-items: center;
    justify-content: center;
    gap: 30px;
    font-family: "Rubik", sans-serif;
  }
  .card {
    width: 560px;
    height: 320px;
    border-radius: 14px;
    position: relative;
    overflow: hidden;
  }

  /* Front */
  .card-front { background: var(--card-dark); color: var(--ink-light); }
  .brand-name {
    position: absolute;
    left: 40px; top: 92px;
    width: 200px;
    font-weight: 700;
    font-size: 27px;
    line-height: 1.05;
    letter-spacing: 2px;
    color: var(--brand-faint);
    text-transform: uppercase;
  }
  .front-divider {
    position: absolute;
    left: 262px; top: 40px;
    width: 1px; height: 140px;
    background: var(--divider);
  }
  .contact {
    position: absolute;
    left: 285px; top: 36px;
    font-size: 12px;
    line-height: 1.55;
    color: var(--ink-muted);
    letter-spacing: .5px;
  }
  .contact-name {
    font-weight: 700;
    font-size: 19px;
    color: var(--ink-light);
    letter-spacing: 1px;
    margin-bottom: 4px;
  }
  .contact-line { display: flex; align-items: center; gap: 7px; }
  .contact-line svg { width: 11px; height: 11px; fill: var(--ink-light); }
  .front-footer {
    position: absolute;
    left: 0; right: 0; bottom: 38px;
    text-align: center;
  }
  .front-title {
    font-weight: 700;
    font-size: 15px;
    letter-spacing: 1px;
    margin-bottom: 8px;
  }
  .front-tagline { font-size: 14px; color: var(--ink-light); }

  /* Back */
  .card-back { background: var(--card-light); color: var(--ink-dark); }
  .service-columns {
    position: absolute;
    left: 34px; top: 30px; right: 24px;
    display: flex;
    gap: 24px;
  }
  .service-list {
    list-style: none;
    font-family: "Roboto Condensed", sans-serif;
    font-weight: 500;
    font-size: 13.5px;
    line-height: 1.42;
  }
  .service-list li { display: flex; align-items: center; gap: 9px; }
  .service-list li::before {
    content: "";
    width: 0; height: 0;
    border-left: 8px solid var(--ink-dark);
    border-top: 5px solid transparent;
    border-bottom: 5px solid transparent;
    flex: none;
  }
  .back-footer {
    position: absolute;
    left: 0; right: 0; bottom: 26px;
    text-align: center;
  }
  .back-title { font-weight: 700; font-size: 16px; margin-bottom: 6px; }
  .back-subtitle { font-size: 15px; letter-spacing: .3px; }
</style>
</head>
<body>

<section class="card card-front">
  <div class="brand-name">Hallmere<br>Refinishers</div>
  <div class="front-divider"></div>
  <div class="contact">
    <div class="contact-name">DANIEL MARCHETTI</div>
    <div class="contact-line">18 ALDER CREEK RD.</div>
    <div class="contact-line">FAIRVIEW, NY 10990</div>
    <div class="contact-line">
      <svg viewBox="0 0 24 24"><path d="M6.6 10.8a15 15 0 0 0 6.6 6.6l2.2-2.2c.3-.3.7-.4 1-.2 1.1.4 2.3.6 3.6.6.6 0 1 .4 1 1V20c0 .6-.4 1-1 1A17 17 0 0 1 3 4c0-.6.4-1 1-1h3.5c.6 0 1 .4 1 1 0 1.3.2 2.5.6 3.6.1.3 0 .7-.2 1z"/></svg>
      555.201.4800
    </div>
    <div class="contact-line">
      <svg viewBox="0 0 24 24"><path d="M7 1h10a2 2 0 0 1 2 2v18a2 2 0 0 1-2 2H7a2 2 0 0 1-2-2V3a2 2 0 0 1 2-2zm0 3v14h10V4zm5 15.5a1 1 0 1 0 0 2 1 1 0 0 0 0-2z"/></svg>
      555.318.7264
    </div>
    <div class="contact-line">
      <svg viewBox="0 0 24 24"><path d="M6 2h9l3 3v4H6zM4 10h16a2 2 0 0 1 2 2v6h-4v4H6v-4H2v-6a2 2 0 0 1 2-2zm4 6v4h8v-4z"/></svg>
      555.201.4815
    </div>
    <div class="contact-line">
      <svg viewBox="0 0 24 24"><path d="M2 5h20v14H2zm2 2v.5l8 5 8-5V7l-8 5z"/></svg>
      STUDIO@HALLMERE.COM
    </div>
  </div>
  <div class="front-footer">
    <div class="front-title">HOME CONTENTS RESTORATION</div>
    <div class="front-tagline">Serving The General Public and The Insurance Industry for Over 40 Years</div>
  </div>
</section>

<section class="card card-back">
  <div class="service-columns">
    <ul class="service-list">
      <li>Antique Repair And Restoration</li>
      <li>Art Cleaning And Remounting</li>
      <li>Art And Mirror Frame Repair</li>
      <li>Chandelier Cleaning And Restoration</li>
      <li>Document Restoration</li>
      <li>Glass, Ceramic, And Mirror Repair</li>
      <li>Hardware Repair And Restoration</li>
      <li>Kitchen Removal And Reinstallation</li>
      <li>Lamp Cleaning And Restoration</li>
      <li>Lamp Shade Replacement</li>
    </ul>
    <ul class="service-list">
      <li>Metal Polishing And Restoration</li>
      <li>Odor Removal And Ozone Services</li>
      <li>Photo Restoration</li>
      <li>Upholstery Cleaning And Deodorizing</li>
      <li>In-house Upholstery And Reupholstery</li>
      <li>Rug Cleaning And Restoration</li>
      <li>Musical Instrument Restoration</li>
      <li>Window Treatment Repair/ Restoration</li>
      <li>Leather Restoration And Replacement</li>
      <li>Piano Restoration And Repair</li>
    </ul>
  </div>
  <div class="back-footer">
    <div class="back-title">On-site Inspections And Desk Review Services</div>
    <div class="back-subtitle">Assessment Reports And Estimates For Repair And Restoration</div>
  </div>
</section>

</body>
</html>
```